Infographic

We are looking for a new concept on a particular PPT slide to communicate a before and after scenario.
Updates

Note that this is a B2B (telecom) technology exercise and are looking for two other ideas to decision makers at billion dollar companies in various verticals. 

Target Market(s)

CIOs, CTOs

```html
<!DOCTYPE html>
<html lang="en">
<head>
<meta charset="utf-8">
<title>Super Nodes: Old World vs New World</title>
<link href="https://fonts.googleapis.com/css2?family=Arimo:wght@400;700&display=swap" rel="stylesheet">
<style>
  :root {
    --band-top: #5b8dbd;
    --band-bottom: #3f74a8;
    --heading-blue: #4a86c0;
    --arrow-blue: #5a8fc2;
    --ring-blue: #a9c8e6;
    --node-light: #e3effa;
    --node-mid: #a7c9e8;
    --node-deep: #3e7fc0;
    --server-grey: #6d7a86;
    --ink: #1d1d1d;
    --brand-grey: #5a6570;
    --white: #ffffff;
    --canvas: #ffffff;
  }
  * { box-sizing: border-box; margin: 0; padding: 0; }
  html, body { width: 1200px; height: 849px; overflow: hidden; background: var(--canvas); }
  body { font-family: "Arimo", Arial, sans-serif; color: var(--ink); }
  .slide { position: relative; width: 1200px; height: 849px; overflow: hidden; }

  .title-band {
    position: absolute; left: 0; top: 0; width: 1200px; height: 120px;
    background: linear-gradient(var(--band-top), var(--band-bottom));
    display: flex; align-items: center; justify-content: center;
  }
  .title-band h1 {
    color: var(--white); font-size: 34px; font-weight: 700; line-height: 1.3; text-align: center;
  }

  .section-heading {
    position: absolute; top: 147px; color: var(--heading-blue);
    font-size: 25px; font-weight: 700; white-space: nowrap;
  }
  .section-heading.old { left: 36px; }
  .section-heading.new { left: 590px; }

  .carrier-hub { position: absolute; left: 70px; top: 265px; width: 280px; height: 280px; }
  .carrier-hub .art {
    position: absolute; inset: 0; border-radius: 50%;
    background: radial-gradient(circle, #e4f0fb 0 62%, #b6d5ef 72%, #7fb2de 84%, #dbeaf8 100%);
  }
  .carrier-hub .label {
    position: absolute; left: 0; right: 0; top: 222px; text-align: center;
    font-size: 22px; line-height: 1.18;
  }

  .migrate-arrow { position: absolute; left: 395px; top: 358px; width: 228px; height: 135px; }
  .migrate-arrow svg { position: absolute; inset: 0; }
  .migrate-arrow .text {
    position: absolute; left: 8px; top: 32px; width: 170px; text-align: center;
    color: var(--white); font-size: 15px; font-weight: 700; line-height: 1.28;
  }

  .network { position: absolute; left: 0; top: 0; width: 1200px; height: 849px; }

  .node {
    position: absolute; width: 110px; height: 110px; border-radius: 50%;
    background: radial-gradient(circle at 50% 42%, var(--server-grey) 0 24%, var(--node-mid) 42%, var(--node-light) 72%);
  }
  .node .name {
    position: absolute; left: 0; right: 0; top: 86px; text-align: center;
    color: var(--white); font-size: 12px;
  }
  .node.top { left: 840px; top: 190px; }
  .node.left { left: 668px; top: 368px; }
  .node.right { left: 1036px; top: 368px; }
  .node.bottom { left: 840px; top: 548px; }

  .customer-icon {
    position: absolute; left: 860px; top: 354px; width: 60px; height: 70px;
    background: var(--node-deep); border: 3px solid #7aa8d6;
  }
  .customer-label {
    position: absolute; left: 775px; top: 450px; width: 240px; text-align: center;
    font-size: 20px; white-space: nowrap;
  }
  .customer-dc {
    position: absolute; left: 884px; top: 484px; width: 30px; height: 62px;
    background: linear-gradient(#eef2f6, #aeb8c2); border: 1px solid #8c96a0;
  }
  .customer-dc-label {
    position: absolute; left: 922px; top: 508px; font-size: 13px; line-height: 1.3;
  }

  .caption { position: absolute; font-size: 16.5px; line-height: 1.35; text-align: center; }
  .caption.old { left: 20px; top: 612px; width: 380px; }
  .caption.new { left: 680px; top: 700px; width: 440px; }

  .brand { position: absolute; left: 38px; top: 752px; display: flex; align-items: center; gap: 12px; }
  .brand .mark { width: 30px; height: 30px; border-radius: 50%; background: var(--node-deep); }
  .brand .name { font-size: 30px; color: var(--brand-grey); white-space: nowrap; }

  .footnote {
    position: absolute; left: 288px; top: 810px; font-size: 14px; font-weight: 700; white-space: nowrap;
  }
</style>
</head>
<body>
<main class="slide">
  <header class="title-band">
    <h1>The leading, proven approach uses intense carrier<br>competition among “super nodes.”</h1>
  </header>

  <h2 class="section-heading old">Old World: Carriers Dictate Prices</h2>
  <h2 class="section-heading new">New World: Competitive Market Lowers Prices</h2>

  <div class="carrier-hub">
    <div class="art" role="img" aria-label="Black rotary telephone inside a light blue circle ringed by blue swirls"></div>
    <p class="label">Carrier at<br>the Center</p>
  </div>

  <div class="migrate-arrow">
    <svg width="228" height="135" viewBox="0 0 228 135" aria-hidden="true">
      <polygon points="0,18 176,18 176,0 228,67.5 176,135 176,117 0,117" fill="var(--arrow-blue)"/>
    </svg>
    <p class="text">Migrate safely from bloated MPLS, optical ring and Internet access services</p>
  </div>

  <svg class="network" viewBox="0 0 1200 849" aria-hidden="true">
    <g fill="none" stroke="var(--ring-blue)">
      <circle cx="895" cy="423" r="170" stroke-width="1.5"/>
      <circle cx="895" cy="423" r="178" stroke-width="2"/>
      <circle cx="895" cy="423" r="185" stroke-width="5"/>
      <circle cx="895" cy="423" r="193" stroke-width="2"/>
    </g>
    <line x1="899" y1="546" x2="899" y2="560" stroke="#8c96a0" stroke-width="1.5"/>
  </svg>

  <div class="node top" role="img" aria-label="Server rack super node"><span class="name">super node</span></div>
  <div class="node left" role="img" aria-label="Server rack super node"><span class="name">super node</span></div>
  <div class="node right" role="img" aria-label="Server rack super node"><span class="name">super node</span></div>
  <div class="node bottom" role="img" aria-label="Server rack super node"><span class="name">super node</span></div>

  <div class="customer-icon" role="img" aria-label="Customer profile icon"></div>
  <p class="customer-label">Customer at the Center</p>
  <div class="customer-dc" role="img" aria-label="Customer data center server"></div>
  <p class="customer-dc-label">Customer’s<br>Data Center</p>

  <p class="caption old">Carrier sells or resells connections to corporate campuses, branches, processing centers, trading partners, application providers</p>
  <p class="caption new">Carrier sells only short tails to third-party data centers that are connected by hundreds of connectivity providers with high performance circuits</p>

  <div class="brand">
    <span class="mark"></span>
    <span class="name">Nodewell Partners</span>
  </div>

  <p class="footnote">Super nodes are transit points within third-party data centers run by leading companies like Vantix, Meridia and Baylock.</p>
</main>
</body>
</html>
```